Online Guide to Events for Adults in Pennsylvania

9GrownupsOnTour is an online event advertisement business for local companies throughout the state to feature their events, music festivals, restaurant, bed & breakfast promotions, wineries and vineyards, theatre and entertainment. The business is geared towards adults. The homepage shall be sleek and elegant, yet user friendly and events searchable on from the homepage. The homepage shall also have an area for local event advertisement spots that rotate every few seconds. Color scheme should include a deep or wine red and some black.

I have attached the current logo and a couple of photos for use. Feel free to use any photos you have available as an example.

A few examples of websites that are similar to what I am looking for:

http://hollowcreekvino.example/

http://www.roamtrevarrow.example/index.asp

I also enjoy the design of many of the websites built by townwright.example.

Target Market(s)

Adults, ages 18 - 65

Industry/Entity Type

Advertising

Number of Pages Required

2 page

Font styles to use
Decorative
Script

Requirements
Must have
• Searchable field on homepage whether it is in the form of a state map with counties, or search by zip code, county, event type and month.
Should not have
• Nothing that appears cartoon like.

```html
<!DOCTYPE html>
<html lang="en">
<head>
<meta charset="utf-8">
<title>9GrownupsOnTour — Online Event Advertisement Business</title>
<link href="https://fonts.googleapis.com/css2?family=Ubuntu:wght@300;400;500;700&family=Open+Sans:wght@400;600&display=swap" rel="stylesheet">
<style>
:root{
  --red:#d42a2a;
  --coral:#ec5438;
  --ink:#2b2b2b;
  --body:#555;
  --muted:#888;
  --line:#e3e3e3;
  --panel:#f7f7f7;
  --page:#e8e8e8;
  --dark:#232323;
  --white:#fff;
}
*{box-sizing:border-box;margin:0;padding:0}
html,body{width:1200px;height:2281px;overflow:hidden}
body{position:relative;background:var(--page);font-family:"Open Sans",Arial,sans-serif;color:var(--body)}
.abs{position:absolute}

/* hero */
.hero{left:0;top:0;width:1200px;height:642px;background:linear-gradient(180deg,#8f7f74 0%,#6f6158 30%,#3e342f 70%,#2a2421 100%)}
.hero-title{left:0;width:1200px;top:262px;text-align:center;color:var(--white);font-family:"Ubuntu",Arial,sans-serif}
.hero-title .big{font-size:54px;font-weight:700;letter-spacing:1px;line-height:60px}
.hero-title .sub{font-size:38px;font-weight:400;line-height:46px}
.hero-btn{left:505px;top:389px;width:190px;height:44px;background:var(--coral);color:var(--white);font-family:"Ubuntu",Arial,sans-serif;font-size:15px;display:flex;align-items:center;justify-content:center;gap:10px;border-radius:2px}
.hero-arrow{top:358px;width:20px;height:26px}

/* header */
.header{left:99px;top:0;width:1002px;height:128px;background:var(--white)}
.brand{left:45px;top:30px;display:flex;align-items:center;gap:8px}
.brand-dot{width:22px;height:22px;border-radius:50%;background:var(--ink)}
.brand-name{font-family:"Ubuntu",Arial,sans-serif;font-size:24px;color:var(--ink);font-weight:500}
.socials{left:547px;top:30px;display:flex;gap:6px}
.socials span{width:24px;height:24px;border-radius:50%;background:#9a9a9a;display:block}
.search-top{left:715px;top:25px;width:167px;height:33px;border:1px solid var(--line);font-size:11px;color:#666;padding:9px 12px}
.signup{left:896px;top:25px;width:78px;height:32px;border:1px solid #bbb;border-radius:3px;font-size:12px;color:#444;text-align:center;line-height:30px}
.nav{font-size:12px;color:#333}
.nav-line{left:517px;top:124px;width:38px;height:3px;background:var(--red)}

/* search panel */
.search-panel{left:99px;top:563px;width:1002px;height:129px;background:var(--panel);border-top:4px solid var(--red)}
.field-label{font-size:13px;color:#333;top:30px}
.field{top:62px;height:39px;border:1px solid var(--line);background:var(--white);font-size:12px;color:#777;padding:11px 12px}
.search-btn{left:864px;top:62px;width:117px;height:39px;background:var(--red);color:var(--white);font-size:16px;text-align:center;line-height:39px;border-radius:2px}

/* welcome */
.welcome{left:99px;top:692px;width:1002px;height:161px;background:var(--white);border-top:1px solid var(--line)}
.welcome h1{position:absolute;left:27px;top:24px;font-family:"Ubuntu",Arial,sans-serif;font-weight:300;font-size:32px;color:#222}
.welcome h1 em{font-style:normal;color:var(--red)}
.welcome p{position:absolute;left:27px;top:76px;width:950px;font-size:12px;line-height:20px;color:#444}

/* category cards */
.card{top:891px;height:423px;background:var(--panel)}
.card.raised{top:889px;height:427px;background:var(--white);box-shadow:0 0 8px rgba(0,0,0,.2);z-index:2}
.card .photo{position:absolute;left:23px;top:20px;width:287px;height:199px}
.card h3{position:absolute;left:0;width:100%;top:240px;text-align:center;font-family:"Ubuntu",Arial,sans-serif;font-weight:400;font-size:16px;color:#333}
.card p{position:absolute;left:25px;right:25px;top:278px;text-align:center;font-size:11px;line-height:20px;color:#555}
.card .more{position:absolute;left:50%;transform:translateX(-50%);top:352px;width:120px;height:44px;border-top:1px solid var(--line);border-bottom:1px solid var(--line);font-size:13px;color:#333;display:flex;align-items:center;justify-content:center;gap:8px}

/* featured events */
.events{left:99px;top:1349px;width:1002px;height:347px;background:var(--white);border-top:3px solid var(--red)}
.events-head{position:absolute;left:0;top:0;width:100%;height:64px;background:var(--panel);border-bottom:1px solid var(--line)}
.events-head h2{position:absolute;left:27px;top:16px;font-family:"Ubuntu",Arial,sans-serif;font-weight:300;font-size:26px;color:#222}
.event{position:absolute;top:112px;width:430px;height:185px}
.date{position:absolute;left:0;top:0;width:127px;height:184px;background:var(--coral);color:var(--white);text-align:center;font-family:"Ubuntu",Arial,sans-serif}
.date .d{font-size:54px;font-weight:700;margin-top:48px;line-height:56px}
.date .m{font-size:22px;font-weight:500}
.pager{position:absolute;left:129px;top:0;width:35px;height:184px;border:1px solid var(--line)}
.pager div{height:30.3px;font-size:12px;color:#888;text-align:center;line-height:30px;border-bottom:1px solid var(--line)}
.pager .arrow{display:flex;align-items:center;justify-content:center}
.pager .on{background:var(--coral);color:var(--white)}
.pager div:last-child{border-bottom:0}
.event h4{position:absolute;left:192px;top:-4px;font-family:"Ubuntu",Arial,sans-serif;font-weight:400;font-size:16px;color:#444}
.event .time{position:absolute;left:192px;top:24px;font-size:11px;color:var(--red);display:flex;align-items:center;gap:5px}
.event p{position:absolute;left:192px;top:52px;width:245px;font-size:11.5px;line-height:20px;color:#444}

/* lower */
.dark-band{left:0;top:1980px;width:1200px;height:301px;background:var(--dark)}
.bottom-line{left:0;top:2277px;width:1200px;height:4px;background:var(--red)}
.lower{left:99px;top:1696px;width:1002px;height:426px;background:var(--white);border-top:1px solid var(--line)}
.sec-title{position:absolute;top:41px;display:flex;align-items:center;gap:12px;font-family:"Ubuntu",Arial,sans-serif;font-size:19px;color:#333}
.ring{width:30px;height:30px;border:1px solid var(--coral);border-radius:50%;display:flex;align-items:center;justify-content:center}
.clip{position:absolute;top:93px;width:286px;height:196px}
.clip-text{position:absolute;top:308px;width:290px;font-size:11px;line-height:20px;color:#444}
.quote{position:absolute;left:686px;top:93px;width:290px;height:150px;border:1px solid var(--line);background:#fafafa;border-radius:3px}
.quote p{position:absolute;left:36px;top:20px;width:238px;font-size:11px;line-height:20px;color:#444}
.quote .mark{position:absolute;left:16px;top:12px;font-family:"Ubuntu",Arial,sans-serif;font-size:28px;color:#ddd;line-height:28px}
.quote-tail{position:absolute;left:895px;top:238px;width:14px;height:14px;background:#fafafa;border-right:1px solid var(--line);border-bottom:1px solid var(--line);transform:rotate(45deg)}
.avatar{position:absolute;left:706px;top:259px;width:80px;height:80px;border-radius:50%;border:2px solid var(--line)}
.author{position:absolute;left:803px;top:269px;font-size:11.5px;color:var(--red);white-space:nowrap}
.author span{color:#555}
.q-nav{position:absolute;left:805px;top:315px;display:flex;gap:4px}
.q-nav div{width:20px;height:20px;border:1px solid var(--line);font-size:11px;color:#555;text-align:center;line-height:18px}

/* footer */
.foot h5{font-family:"Ubuntu",Arial,sans-serif;font-weight:400;font-size:19px;color:#ddd;letter-spacing:.5px}
.foot p{font-size:12px;color:#aaa;line-height:18px}
.foot .links{font-size:13px;color:#aaa;margin-top:22px}
.follow{left:841px;top:2172px;display:flex;align-items:center;gap:18px}
.follow h5{font-family:"Ubuntu",Arial,sans-serif;font-weight:400;font-size:19px;color:#ddd}
.follow .sq{display:flex;gap:5px}
.follow .sq span{width:23px;height:23px;background:#eee;border-radius:3px;display:block}
</style>
</head>
<body>

<div class="abs hero" role="img" aria-label="City skyline of tall buildings under a hazy sky"></div>
<svg class="abs hero-arrow" style="left:46px" viewBox="0 0 20 26"><path d="M14 4 L6 13 L14 22" stroke="#fff" stroke-opacity=".6" stroke-width="2" fill="none"/></svg>
<svg class="abs hero-arrow" style="left:1144px" viewBox="0 0 20 26"><path d="M6 4 L14 13 L6 22" stroke="#fff" stroke-opacity=".6" stroke-width="2" fill="none"/></svg>
<div class="abs hero-title"><div class="big">ONLINE EVENT</div><div class="sub">Advertisement Business</div></div>
<div class="abs hero-btn">GETTING STARTED
  <svg width="14" height="14" viewBox="0 0 14 14"><circle cx="7" cy="7" r="7" fill="#fff"/><path d="M5.5 4 L8.5 7 L5.5 10" stroke="#ec5438" stroke-width="1.8" fill="none"/></svg>
</div>

<header class="abs header">
  <div class="abs brand"><span class="brand-dot"></span><span class="brand-name">9GrownupsOnTour</span></div>
  <div class="abs socials"><span></span><span></span><span></span><span></span><span></span></div>
  <div class="abs search-top">SEARCH
    <svg style="position:absolute;right:10px;top:10px" width="12" height="12" viewBox="0 0 12 12"><circle cx="5" cy="5" r="3.8" stroke="#555" stroke-width="1.5" fill="none"/><path d="M8 8 L11 11" stroke="#555" stroke-width="1.6"/></svg>
  </div>
  <div class="abs signup">SIGN UP</div>
</header>
<nav class="abs nav" style="left:0;top:0;width:1200px;height:128px">
  <span class="abs" style="left:519px;top:87px">HOME</span>
  <span class="abs" style="left:605px;top:87px">ABOUT EVENT</span>
  <span class="abs" style="left:737px;top:87px">MUSIC FESTIVALS</span>
  <span class="abs" style="left:889px;top:87px">SERVICES</span>
  <span class="abs" style="left:1000px;top:87px">CONTACT US</span>
</nav>
<div class="abs nav-line"></div>

<section class="abs search-panel">
  <span class="abs field-label" style="left:22px">SEARCH BY ZIP CODE</span>
  <span class="abs field-label" style="left:231px">COUNTY</span>
  <span class="abs field-label" style="left:441px">EVENT TYPE</span>
  <span class="abs field-label" style="left:648px">MONTH</span>
  <div class="abs field" style="left:21px;width:197px">search by zip code</div>
  <div class="abs field" style="left:231px;width:197px">All<svg style="position:absolute;right:12px;top:16px" width="8" height="5"><path d="M0 0 H8 L4 5Z" fill="#666"/></svg></div>
  <div class="abs field" style="left:440px;width:197px">All<svg style="position:absolute;right:12px;top:16px" width="8" height="5"><path d="M0 0 H8 L4 5Z" fill="#666"/></svg></div>
  <div class="abs field" style="left:647px;width:196px">month<svg style="position:absolute;right:10px;top:13px" width="11" height="11" viewBox="0 0 11 11"><rect x=".5" y="1.5" width="10" height="9" fill="none" stroke="#888"/><path d="M.5 4 H10.5 M3 5.5v4 M5.5 5.5v4 M8 5.5v4" stroke="#888"/></svg></div>
  <div class="abs search-btn">SEARCH</div>
</section>

<section class="abs welcome">
  <h1>Welcome To <em>9GrownupsOnTour</em></h1>
  <p>Lorem ipsum dolor sit amet, consectetur adipiscing elit, sed do eiusmod tempor incididunt ut labore et dolore magna aliqua. Ut enim ad minim veniam, quis nostrud exercitation ullamco laboris nisi ut aliquip ex ea commodo consequat. Duis aute irure dolor in reprehenderit in voluptate velit esse cillum dolore eu fugiat nulla pariatur. Excepteur sint occaecat cupidatat non proident, sunt in culpa qui officia deserunt mollit anim id est laborum</p>
</section>

<article class="abs card" style="left:99px;width:332px">
  <div class="photo" role="img" aria-label="Concert crowd with raised hands under stage lights" style="background:radial-gradient(circle at 40% 20%,#d8cbb0,#6b5a44 45%,#1c1711 90%)"></div>
  <h3>MUSIC FESTIVALS</h3>
  <p>Lorem ipsum dolor sit amet, consec teer adipiscing. Prsent vestibulum molestie la my hendrerit. mauris haselllus. Porta. Lorem ipsum dolor</p>
  <div class="more">READ MORE <svg width="12" height="12"><circle cx="6" cy="6" r="6" fill="#333"/><path d="M5 3.5 L7.5 6 L5 8.5" stroke="#fff" stroke-width="1.5" fill="none"/></svg></div>
</article>
<article class="abs card raised" style="left:431px;width:338px">
  <div class="photo" role="img" aria-label="Plated tomato and vegetable appetizer on a white plate" style="left:24px;top:22px;background:linear-gradient(135deg,#e9e9ea,#d9c6b9 40%,#cf6548 60%,#e7e4e0)"></div>
  <h3 style="top:242px">BED &amp; BREAKFAST PROMOTIONS</h3>
  <p style="top:280px">Lorem ipsum dolor sit amet, consec teer adipiscing. Prsent vestibulum molestie la my hendrerit. mauris haselllus. Porta. Lorem ipsum dolor</p>
  <div class="more" style="top:354px">READ MORE <svg width="12" height="12"><circle cx="6" cy="6" r="6" fill="#333"/><path d="M5 3.5 L7.5 6 L5 8.5" stroke="#fff" stroke-width="1.5" fill="none"/></svg></div>
</article>
<article class="abs card" style="left:769px;width:332px">
  <div class="photo" role="img" aria-label="Wine bottle, glass, cheese and bread by candlelight" style="background:linear-gradient(90deg,#1c1712,#3a2a1c 50%,#6d4f2c 75%,#1d1710)"></div>
  <h3>WINERIES AND VINEYARDS</h3>
  <p>Lorem ipsum dolor sit amet, consec teer adipiscing. Prsent vestibulum molestie la my hendrerit. mauris haselllus. Porta. Lorem ipsum dolor</p>
  <div class="more">READ MORE <svg width="12" height="12"><circle cx="6" cy="6" r="6" fill="#333"/><path d="M5 3.5 L7.5 6 L5 8.5" stroke="#fff" stroke-width="1.5" fill="none"/></svg></div>
</article>

<section class="abs events">
  <div class="events-head"><h2>Feature Their Events</h2></div>
  <div class="event" style="left:26px">
    <div class="date"><div class="d">14</div><div class="m">June</div></div>
    <div class="pager">
      <div class="arrow"><svg width="9" height="6"><path d="M1 5 L4.5 1.5 L8 5" stroke="#333" stroke-width="1.6" fill="none"/></svg></div>
      <div class="on">01</div><div>02</div><div>03</div><div>04</div>
      <div class="arrow"><svg width="9" height="6"><path d="M1 1 L4.5 4.5 L8 1" stroke="#333" stroke-width="1.6" fill="none"/></svg></div>
    </div>
    <h4>Nemo Enim Ipsam Voluptatem</h4>
    <div class="time"><svg width="10" height="10"><circle cx="5" cy="5" r="4" stroke="#d42a2a" stroke-width="1.4" fill="none"/><path d="M5 2.5V5H7" stroke="#d42a2a" stroke-width="1.2" fill="none"/></svg>19.00 pm – 21.00 pm</div>
    <p>Lorem ipsum dolor sit amet, consectetur adipiscing elit, sed do eiusmod tempor incid-idunt ut labore et dolore magna aliqua. Ut enim ad minim veniam, quis nostrud exerci-tation ullamco laboris nisi ut aliquip ex ea commodo consequat.</p>
  </div>
  <div class="event" style="left:532px">
    <div class="date"><div class="d">14</div><div class="m">June</div></div>
    <div class="pager">
      <div class="arrow"><svg width="9" height="6"><path d="M1 5 L4.5 1.5 L8 5" stroke="#333" stroke-width="1.6" fill="none"/></svg></div>
      <div class="on">01</div><div>02</div><div>03</div><div>04</div>
      <div class="arrow"><svg width="9" height="6"><path d="M1 1 L4.5 4.5 L8 1" stroke="#333" stroke-width="1.6" fill="none"/></svg></div>
    </div>
    <h4>Nemo Enim Ipsam Voluptatem</h4>
    <div class="time"><svg width="10" height="10"><circle cx="5" cy="5" r="4" stroke="#d42a2a" stroke-width="1.4" fill="none"/><path d="M5 2.5V5H7" stroke="#d42a2a" stroke-width="1.2" fill="none"/></svg>19.00 pm – 21.00 pm</div>
    <p>Lorem ipsum dolor sit amet, consectetur adipiscing elit, sed do eiusmod tempor incid-idunt ut labore et dolore magna aliqua. Ut enim ad minim veniam, quis nostrud exerci-tation ullamco laboris nisi ut aliquip ex ea commodo consequat.</p>
  </div>
</section>

<div class="abs dark-band"></div>

<section class="abs lower">
  <div class="sec-title" style="left:25px"><span class="ring"><svg width="14" height="10"><rect x="0" y="1" width="9" height="8" rx="1" fill="#ec5438"/><path d="M9 5 L14 1 V9Z" fill="#ec5438"/></svg></span>Theatre And Entertainment</div>
  <div class="clip" style="left:26px;background:linear-gradient(160deg,#4a4f5a,#9b2a2a 55%,#c8352f)" role="img" aria-label="Audience watching a film in red cinema seats">
    <svg style="position:absolute;left:122px;top:77px" width="44" height="44"><circle cx="22" cy="22" r="21" fill="#fff" fill-opacity=".8"/><path d="M17 13 L31 22 L17 31Z" fill="#555"/></svg>
  </div>
  <div class="clip" style="left:351px;background:linear-gradient(180deg,#5f87b3,#8ea6c0 40%,#2b2a2a 75%,#1a1716)" role="img" aria-label="Seated audience facing a lit stage"></div>
  <p class="clip-text" style="left:26px">Lorem ipsum dolor sit amet, consectetur adipiscing elit, sed do eiusmod tempor incididunt ut labore et dolore magna aliqua. Ut enim ad minim veniam, quis nostrud exercitation ullamco laboris nisi ut aliquip</p>
  <p class="clip-text" style="left:351px">Lorem ipsum dolor sit amet, consectetur adipiscing elit, sed do eiusmod tempor incididunt ut labore et dolore magna aliqua. Ut enim ad minim veniam, quis nostrud exercitation ullamco laboris nisi ut aliquip</p>

  <div class="sec-title" style="left:682px"><span class="ring"><svg width="14" height="13"><ellipse cx="7" cy="6" rx="6" ry="4.5" stroke="#ec5438" stroke-width="1.3" fill="none"/><path d="M4 10 L3 13 L7 10.3" fill="#ec5438"/></svg></span>Testimonials</div>
  <div class="quote"><span class="mark">&ldquo;</span><p>Lorem ipsum dolor sit amet, consectetur adipiscing elit, sed do eiusmod tempor incididunt ut labore et dolore magna aliqua. Ut enim ad minim veniam, quis nostrud exercitation Lorem ipsum dolor sit amet,</p></div>
  <div class="quote-tail"></div>
  <div class="avatar" role="img" aria-label="Portrait of the reviewer" style="background:linear-gradient(180deg,#d9d9d9,#9aa4b0 55%,#2d3440)"></div>
  <div class="author">Sam Avery - <span>9GrownupsOnTour</span></div>
  <div class="q-nav"><div>&lsaquo;</div><div>&rsaquo;</div></div>
</section>

<footer>
  <div class="abs foot" style="left:97px;top:2162px">
    <h5>COPYRIGHT</h5>
    <p>(c) 2015 9GrownupsOnTour. All rights reserved.</p>
    <div class="links">Home &nbsp;/&nbsp; Artist Bio &nbsp;/&nbsp; View events &nbsp;/&nbsp; Contacts</div>
  </div>
  <div class="abs foot" style="left:456px;top:2162px">
    <h5>ADDRESS</h5>
    <p>412 Marlow Lane, Harrowgate, PA 17602</p>
    <p style="margin-top:14px">+1 800 5550 132</p>
  </div>
  <div class="abs follow"><h5>FOLLOW US</h5><div class="sq"><span></span><span></span><span></span></div></div>
</footer>
<div class="abs bottom-line"></div>

</body>
</html>
```